Brightwave Reach - Business Card

We need a business card for a Social Media Marketing company that specializes in online marketing for small businesses in Canada using common Social Media platforms such as Pixlora, Chatterly, Blinkpost & Quibber.

I have uploaded a copy of our logo which I would like utilized in the business card. We would like the business card to be modern yet classy design.

Our website is www.brightwavereach.ca

Industry/Entity Type

Marketing

Contact Information for Business Card

Email: info@brightwavereach.ca
Website: www.brightwavereach.ca
Telephone: 604-555-0193

Colors

Designer to choose colors to be used in the design.

Requirements
Must have
• Social Media icons on reverse
• Please add some designs with color.

```html
<!DOCTYPE html>
<html lang="en">
<head>
<meta charset="utf-8">
<title>Brightwave Reach – Business Card</title>
<link href="https://fonts.googleapis.com/css2?family=Open+Sans:wght@400;600;800&display=swap" rel="stylesheet">
<style>
  :root {
    --stage-top: #1c1c1c;
    --stage-bottom: #050505;
    --card: #ffffff;
    --card-back: #f7f7f7;
    --ink: #3e3e3e;
    --ink-soft: #7a7a7a;
    --icon: #555555;
    --accent: #c8372d;
    --accent-soft: #f3d9d6;
  }
  * { margin: 0; padding: 0; box-sizing: border-box; }
  html, body { width: 1200px; height: 900px; overflow: hidden; }
  body {
    position: relative;
    background: linear-gradient(180deg, var(--stage-top) 0%, var(--stage-bottom) 100%);
    font-family: "Open Sans", Arial, sans-serif;
  }
  .card {
    position: absolute;
    top: 306px;
    width: 440px;
    height: 271px;
    border-radius: 12px;
    background: var(--card);
    overflow: hidden;
  }
  .card--front { left: 149px; }
  .card--back { left: 608px; width: 441px; background: var(--card-back); }

  .wordmark {
    position: absolute;
    display: flex;
    align-items: center;
    gap: 8px;
    color: var(--ink);
    font-weight: 800;
    font-size: 19px;
    line-height: 21px;
    letter-spacing: 0.5px;
    text-transform: uppercase;
    text-align: center;
  }
  .wordmark__square {
    width: 10px; height: 10px;
    background: var(--accent);
  }
  .card--front .wordmark { left: 50px; top: 103px; }
  .card--back .wordmark { left: 148px; top: 98px; }

  .person {
    position: absolute;
    left: 240px;
    top: 80px;
  }
  .person__name {
    font-size: 15px;
    font-weight: 600;
    color: var(--ink);
    line-height: 19px;
  }
  .person__title {
    font-size: 12px;
    color: var(--ink-soft);
    line-height: 16px;
  }
  .contact {
    position: absolute;
    left: 242px;
    top: 145px;
    list-style: none;
  }
  .contact__item {
    display: flex;
    align-items: center;
    gap: 5px;
    font-size: 12px;
    color: var(--ink-soft);
    line-height: 16px;
  }
  .contact__icon { width: 9px; height: 9px; fill: var(--icon); }

  .socials {
    position: absolute;
    left: 0;
    right: 0;
    top: 168px;
    display: flex;
    justify-content: center;
    gap: 16px;
    list-style: none;
  }
  .socials__item {
    display: flex;
    align-items: center;
    gap: 5px;
    font-size: 11px;
    color: var(--ink-soft);
    line-height: 14px;
  }
  .socials__dot {
    width: 9px; height: 9px;
    border-radius: 50%;
    background: var(--accent);
  }
  .back-band {
    position: absolute;
    left: 0; right: 0; bottom: 0;
    height: 52px;
    background: linear-gradient(180deg, var(--accent-soft) 0%, #e8b3ad 100%);
  }
</style>
</head>
<body>
  <section class="card card--front" aria-label="Card front">
    <div class="wordmark">
      <span class="wordmark__square"></span>
      <span>Brightwave<br>Reach</span>
    </div>
    <div class="person">
      <p class="person__name">Daniel Mercer</p>
      <p class="person__title">Managing Director</p>
    </div>
    <ul class="contact">
      <li class="contact__item">
        <svg class="contact__icon" viewBox="0 0 10 10"><path d="M1 3 Q5 0 9 3 L8 4.5 L6.5 3.8 L6.5 3 Q5 2.6 3.5 3 L3.5 3.8 L2 4.5 Z M2.5 5 H7.5 L8.5 9 H1.5 Z"/></svg>
        604-555-0193
      </li>
      <li class="contact__item">
        <svg class="contact__icon" viewBox="0 0 10 10"><path d="M0.5 2 H9.5 V8.5 H0.5 Z M1.5 3 V7.5 H8.5 V3 L5 5.6 Z"/></svg>
        info@brightwavereach.ca
      </li>
      <li class="contact__item">
        <svg class="contact__icon" viewBox="0 0 10 10"><circle cx="5" cy="5" r="4.5"/><path d="M2.5 3 Q4 2 4.5 4 Q3 5 4 7 L3 8 Q1.2 6 2.5 3 Z M6 2 Q8 3 7.8 5 L6.5 5.5 Q5.5 4 6 2 Z" fill="#fff"/></svg>
        www.brightwavereach.ca
      </li>
    </ul>
  </section>

  <section class="card card--back" aria-label="Card back">
    <div class="wordmark">
      <span class="wordmark__square"></span>
      <span>Brightwave<br>Reach</span>
    </div>
    <ul class="socials" aria-label="Social platforms">
      <li class="socials__item"><span class="socials__dot"></span>Pixlora</li>
      <li class="socials__item"><span class="socials__dot"></span>Chatterly</li>
      <li class="socials__item"><span class="socials__dot"></span>Blinkpost</li>
      <li class="socials__item"><span class="socials__dot"></span>Quibber</li>
    </ul>
    <div class="back-band"></div>
  </section>
</body>
</html>
```